Business Card Design Project 4thKVL

Business card that looks professional but stands out!

Industry/Entity Type

Business

Requirements
Must have
• Tailor to Realtors
loan products on the back of the card

```html
<!DOCTYPE html>
<html lang="en">
<head>
<meta charset="utf-8">
<title>4thKVL Home Loans – Business Card</title>
<link href="https://fonts.googleapis.com/css2?family=Arimo:wght@400;700&display=swap" rel="stylesheet">
<style>
  :root {
    --bg: #2b2b2b;
    --brand-blue: #0b4f9c;
    --paper: #ffffff;
    --paper-shade: #eeeeee;
    --rule-grey: #9a9a9a;
    --back-grey-light: #b4b4b4;
    --back-grey-dark: #8c8c8c;
    --ink-grey: #7a7a7a;
    --text-light: #ffffff;
  }
  * { box-sizing: border-box; margin: 0; padding: 0; }
  html, body { width: 1200px; height: 900px; overflow: hidden; }
  body {
    background: var(--bg);
    font-family: "Arimo", Arial, sans-serif;
    display: flex;
    flex-direction: column;
    align-items: center;
    justify-content: center;
    gap: 30px;
  }
  .card {
    width: 700px;
    height: 400px;
    position: relative;
    overflow: hidden;
  }

  /* Front */
  .card-front { background: var(--brand-blue); }
  .front-top {
    position: absolute; left: 0; top: 0; width: 100%; height: 190px;
    background: linear-gradient(180deg, var(--paper) 60%, var(--paper-shade));
  }
  .brand {
    position: absolute; left: 200px; top: 62px;
    display: flex; align-items: center; gap: 14px;
  }
  .brand-square {
    width: 30px; height: 30px;
    background: var(--brand-blue);
  }
  .brand-name {
    color: var(--brand-blue);
    font-weight: 700;
    font-size: 34px;
    line-height: 1;
    white-space: nowrap;
  }
  .tagline {
    position: absolute; left: 30px; top: 142px;
    color: var(--ink-grey); font-size: 14px; line-height: 1.35;
  }
  .front-rule {
    position: absolute; left: 0; top: 190px; width: 390px; height: 8px;
    background: var(--rule-grey);
  }
  .contact-list {
    position: absolute; right: 70px; top: 210px;
    list-style: none; color: var(--text-light); font-size: 15px;
  }
  .contact-list li { display: flex; align-items: center; gap: 10px; height: 24px; }
  .contact-list svg { width: 16px; height: 16px; fill: var(--text-light); }
  .person {
    position: absolute; left: 30px; top: 270px; color: var(--text-light);
  }
  .person-name { font-size: 28px; font-weight: 700; }
  .person-title { font-size: 16px; margin-top: 2px; }
  .person-address {
    display: flex; gap: 10px; margin-top: 12px; font-size: 15px; line-height: 1.3;
  }
  .person-address svg { width: 16px; height: 20px; fill: var(--text-light); flex: none; margin-top: 2px; }

  /* Back */
  .card-back {
    background: radial-gradient(ellipse at 55% 30%, var(--back-grey-light), var(--back-grey-dark));
  }
  .back-stripe {
    position: absolute; left: 0; top: 0; width: 70px; height: 100%;
    background: var(--brand-blue);
  }
  .programs {
    position: absolute; left: 100px; top: 45px; right: 20px;
    display: flex; gap: 22px; color: var(--text-light);
  }
  .program-column { white-space: nowrap; }
  .programs-heading { font-size: 19px; font-weight: 700; margin-bottom: 2px; line-height: 1.2; }
  .program-list { list-style: disc; padding-left: 22px; font-size: 16px; line-height: 1.3; }
</style>
</head>
<body>

<section class="card card-front" aria-label="Business card front">
  <div class="front-top">
    <div class="brand">
      <div class="brand-square"></div>
      <div class="brand-name">4thKVL Home Loans</div>
    </div>
    <p class="tagline">We make the journey of buying a home or refinancing a mortgage easy.<br>You can depend on us to help you find the perfect loan program for you.</p>
  </div>
  <div class="front-rule"></div>

  <ul class="contact-list">
    <li><svg viewBox="0 0 16 16"><path d="M3 1h3l1 4-2 1c1 2 3 4 5 5l1-2 4 1v3c0 1-1 2-2 2C7 15 1 9 1 3c0-1 1-2 2-2z"/></svg>555.210.4400</li>
    <li><svg viewBox="0 0 16 16"><rect x="4" y="1" width="8" height="4"/><rect x="1" y="6" width="14" height="6" rx="1"/><rect x="4" y="10" width="8" height="5"/></svg>555.210.4401</li>
    <li><svg viewBox="0 0 16 16"><path d="M1 3h14v10H1z M2 4l6 5 6-5" stroke="#0b4f9c" stroke-width="1"/></svg>info@4thkvl.com</li>
    <li><svg viewBox="0 0 16 16"><circle cx="8" cy="8" r="7"/><path d="M1 8h14M8 1c-3 3-3 11 0 14M8 1c3 3 3 11 0 14" stroke="#0b4f9c" fill="none"/></svg>www.4thkvl.com</li>
  </ul>

  <div class="person">
    <h1 class="person-name">Dana Whitfield</h1>
    <p class="person-title">Manager</p>
    <div class="person-address">
      <svg viewBox="0 0 16 20"><path d="M8 0a7 7 0 0 1 7 7c0 5-7 13-7 13S1 12 1 7a7 7 0 0 1 7-7zm0 4a3 3 0 1 0 0 6 3 3 0 0 0 0-6z"/></svg>
      <p>Address 48 Elm St, Suite 210<br>Harbor CA 90210 LAKESIDE</p>
    </div>
  </div>
</section>

<section class="card card-back" aria-label="Business card back">
  <div class="back-stripe"></div>
  <div class="programs">
    <div class="program-column">
      <h2 class="programs-heading">LOAN PROGRAMS</h2>
      <ul class="program-list">
        <li>Jumbo Mortgages</li><li>30 Year Fixed</li><li>15 Year Fixed</li><li>FHA Home Loan</li><li>VA 30 Year Fixed</li><li>HARP 2.0</li><li>Reverse Mortgages</li><li>FHA Home Loan</li><li>VA 30 Year Fixed</li><li>HARP 2.0</li><li>Reverse Mortgages</li>
      </ul>
    </div>
    <div class="program-column">
      <ul class="program-list">
        <li>Jumbo Mortgages</li><li>30 Year Fixed</li><li>15 Year Fixed</li><li>FHA Home Loan</li><li>VA 30 Year Fixed</li><li>HARP 2.0</li><li>Reverse Mortgages</li><li>FHA Home Loan</li><li>VA 30 Year Fixed</li><li>HARP 2.0</li><li>Reverse Mortgages</li>
      </ul>
    </div>
    <div class="program-column">
      <ul class="program-list">
        <li>Jumbo Mortgages</li><li>30 Year Fixed</li><li>15 Year Fixed</li><li>FHA Home Loan</li><li>VA 30 Year Fixed</li><li>HARP 2.0</li><li>Reverse Mortgages</li><li>FHA Home Loan</li><li>VA 30 Year Fixed</li><li>HARP 2.0</li><li>Reverse Mortgages</li>
      </ul>
    </div>
  </div>
</section>

</body>
</html>
```